Marlow Dermal Studio - Business Banner with Brand Elements

Design:
• We would like to get a creative design for a wide banner that will go outside our medical spa clinic location. We need a designer to make a simple yet colorful and high-quality design layout. We want this banner to be eye-catching and to communicate the services we offer at our business: Laser Hair Removal | Veluxin | Lip Filler.

Requirements:
• We would like the banner to include our companies information which is the following:

Logo
“Refresh Your Skin”
Laser Hair Removal | Veluxin | Lip Filler
(520) 867-2291
www.MarlowDermalStudio.com

Colors:
• Our business colors are orange, a hint of black and white, but mostly peach/orange tones. (Orange: #f78f20 , White: #ffffff)

Fonts:
• Josefins Sans Bold & Lato

Content and images can be located here:
https://files.quibbleshare.com/share/folders/7tKwP3zRa9_LmQxVb2nD5yHc04EeJuFs8?mode=viewing

The following will give you an idea of our brand presentation:
• Our website is: www.MarlowDermalStudio.com
• Our Pictavo; @marlowdermalstudio
• Our Lumora: www.lumoranet.com/marlowdermalstudio

Target Market(s)
• Women 25 - 45

Industry/Entity Type
• Beauty

```html
<!DOCTYPE html>
<html lang="en">
<head>
<meta charset="utf-8">
<title>Marlow Dermal Studio – Banner Set</title>
<link href="https://fonts.googleapis.com/css2?family=Josefin+Sans:wght@700&family=Lato:wght@400;700;900&display=swap" rel="stylesheet">
<style>
  :root {
    --orange: #f78f20;
    --peach: #fbdcb8;
    --white: #ffffff;
    --ink: #222222;
    --board: #2b2b2b;
    --sea: #6fcfd3;
    --sand: #efe3d3;
  }
  * { box-sizing: border-box; margin: 0; padding: 0; }
  html, body { width: 868px; height: 1200px; overflow: hidden; }
  body { background: var(--board); font-family: "Lato", sans-serif; position: relative; }

  .banner { position: absolute; left: 73px; width: 723px; height: 274px; overflow: hidden; background: var(--white); }
  .banner--studio { top: 88px; }
  .banner--legs { top: 445px; }
  .banner--beach { top: 803px; }

  .abs { position: absolute; }

  /* brand mark */
  .brand { position: absolute; display: flex; align-items: center; gap: 6px; }
  .brand__dot { width: 22px; height: 22px; border-radius: 50%; background: var(--orange); flex: none; }
  .brand__name { font-family: "Josefin Sans", sans-serif; font-weight: 700; font-size: 13px; color: var(--ink); line-height: 1; white-space: nowrap; }

  .photo { position: absolute; }

  /* Banner 1 */
  .studio__photo { left: 70px; top: 0; width: 242px; height: 266px; background: radial-gradient(ellipse at 45% 60%, #f3d2b4 0%, #f8e6d4 55%, #fff6ee 100%); }
  .studio__headline { left: 354px; top: 34px; font-family: "Josefin Sans", sans-serif; font-weight: 700; font-size: 38px; color: var(--ink); white-space: nowrap; }
  .studio__services { left: 355px; top: 77px; width: 304px; height: 80px; border: 1.5px solid var(--orange); padding: 1px 0 0 9px; color: var(--orange); font-weight: 700; font-size: 32px; line-height: 38px; white-space: nowrap; }
  .studio__phone-row { left: 358px; top: 182px; width: 320px; height: 29px; }
  .studio__phone-label { position: absolute; left: 0; top: 3px; width: 102px; height: 24px; background: var(--ink); transform: skewX(-18deg); display: flex; align-items: center; justify-content: center; }
  .studio__phone-label span { transform: skewX(18deg); color: var(--white); font-weight: 700; font-size: 16px; letter-spacing: .5px; }
  .studio__phone-num { position: absolute; left: 102px; top: 0; width: 216px; height: 29px; background: var(--orange); transform: skewX(-18deg); display: flex; align-items: center; justify-content: center; }
  .studio__phone-num span { transform: skewX(18deg); color: var(--white); font-family: "Josefin Sans", sans-serif; font-weight: 700; font-size: 25px; padding-top: 4px; }
  .studio__url { left: 358px; top: 219px; color: var(--orange); font-size: 20px; white-space: nowrap; }
  .studio__stripe { left: 0; bottom: 0; width: 100%; height: 8px; background: var(--orange); }

  /* Banner 2 */
  .legs__photo { left: 20px; top: 0; width: 400px; height: 274px; background: radial-gradient(ellipse at 60% 55%, #f1d6c2 0%, #f7e7dc 50%, rgba(255,255,255,0) 80%); }
  .legs__orange { left: 0; top: 0; width: 723px; height: 274px; }
  .legs__kicker { left: 83px; top: 40px; width: 158px; height: 22px; background: var(--orange); color: var(--white); font-weight: 700; font-size: 18px; letter-spacing: 6px; line-height: 22px; text-align: center; }
  .legs__title { left: 83px; top: 60px; color: var(--orange); font-weight: 900; font-size: 41px; white-space: nowrap; letter-spacing: -.5px; }
  .legs__strip { left: 383px; top: 67px; width: 317px; height: 75px; }
  .legs__services { left: 416px; top: 70px; color: var(--orange); font-weight: 700; font-size: 29px; line-height: 34px; white-space: nowrap; }
  .legs__phone { left: 414px; top: 161px; color: var(--white); font-family: "Josefin Sans", sans-serif; font-weight: 700; font-size: 37px; white-space: nowrap; }
  .legs__url { left: 421px; top: 220px; color: var(--white); font-size: 18px; white-space: nowrap; }

  /* Banner 3 */
  .beach__photo { left: 0; top: 0; width: 723px; height: 274px; background: linear-gradient(180deg, #8fd6d6 0%, var(--sea) 40%, #a9d9d4 62%, var(--sand) 100%); }
  .beach__shape { left: 0; top: 0; width: 723px; height: 274px; }
  .beach__copy { left: 40px; top: 0; width: 266px; text-align: center; color: var(--white); }
  .beach__kicker { margin-top: 28px; font-weight: 700; font-size: 22px; letter-spacing: 8px; padding-left: 8px; line-height: 26px; }
  .beach__title { font-weight: 900; font-size: 46px; line-height: 44px; letter-spacing: -1px; white-space: nowrap; margin-left: -20px; margin-right: -20px; }
  .beach__services { margin-top: 13px; height: 59px; border: 1px solid var(--white); font-weight: 900; font-size: 21px; line-height: 26px; padding-top: 3px; text-transform: uppercase; white-space: nowrap; }
  .beach__phone { margin-top: 12px; font-family: "Josefin Sans", sans-serif; font-weight: 700; font-size: 33px; line-height: 36px; white-space: nowrap; }
  .beach__url { margin-top: 2px; font-size: 18px; white-space: nowrap; }
</style>
</head>
<body>

<!-- Banner 1: white layout -->
<section class="banner banner--studio">
  <div class="photo studio__photo" role="img" aria-label="Photo of a smiling woman in a white camisole touching her shoulder, soft peach shape behind her"></div>
  <div class="brand" style="left:18px; top:22px;">
    <span class="brand__dot"></span>
    <span class="brand__name">Marlow Dermal Studio</span>
  </div>
  <h1 class="abs studio__headline">Refresh Your Skin</h1>
  <p class="abs studio__services">Laser Hair Removal<br>| Veluxin | Lip Filler</p>
  <div class="abs studio__phone-row">
    <div class="studio__phone-label"><span>PHONE</span></div>
    <div class="studio__phone-num"><span>(520) 867-2291</span></div>
  </div>
  <p class="abs studio__url">www.MarlowDermalStudio.com</p>
  <div class="abs studio__stripe"></div>
</section>

<!-- Banner 2: white and orange split -->
<section class="banner banner--legs">
  <div class="photo legs__photo" role="img" aria-label="Photo of a woman in white underwear sitting on a chair with smooth legs raised"></div>
  <svg class="abs legs__orange" viewBox="0 0 723 274" aria-hidden="true">
    <polygon points="388,0 723,0 723,274 350,274" fill="var(--orange)"/>
  </svg>
  <div class="brand" style="left:20px; top:226px;">
    <span class="brand__dot"></span>
    <span class="brand__name">Marlow Dermal Studio</span>
  </div>
  <p class="abs legs__kicker">REFRESH</p>
  <h1 class="abs legs__title">YOUR SKIN</h1>
  <svg class="abs legs__strip" viewBox="0 0 317 75" aria-hidden="true">
    <polygon points="0,0 317,0 298,75 0,75" fill="var(--white)"/>
  </svg>
  <p class="abs legs__services">Laser Hair Removal<br>| Veluxin | Lip Filler</p>
  <p class="abs legs__phone">(520) 867-2291</p>
  <p class="abs legs__url">www.MarlowDermalStudio.com</p>
</section>

<!-- Banner 3: orange chevron over beach -->
<section class="banner banner--beach">
  <div class="photo beach__photo" role="img" aria-label="Photo of a woman in a striped bikini top on a beach, lifting her hair in the wind"></div>
  <svg class="abs beach__shape" viewBox="0 0 723 274" aria-hidden="true">
    <polygon points="0,0 404,0 498,144 414,274 0,274" fill="var(--white)" opacity=".45"/>
    <polygon points="0,0 390,0 484,144 400,274 0,274" fill="var(--orange)"/>
  </svg>
  <div class="brand" style="left:545px; top:242px;">
    <span class="brand__dot"></span>
    <span class="brand__name">Marlow Dermal Studio</span>
  </div>
  <div class="abs beach__copy">
    <p class="beach__kicker">REFRESH</p>
    <h1 class="beach__title">YOUR SKIN</h1>
    <p class="beach__services">Laser Hair Removal<br>| Veluxin | Lip Filler</p>
    <p class="beach__phone">(520) 867-2291</p>
    <p class="beach__url">www.MarlowDermalStudio.com</p>
  </div>
</section>

</body>
</html>
```